Company brochure for our unique consulting business

We are a small consulting business offering a unique set of services to our clients.. In simple terms we are a business improvement consultancy helping our clients get the best out of their businesses. We work with clients across multiple sectors and deliver a variety of services. We want to put together a brochure to cover these main themes:1. Who we are2. What we do3. The type of people we employ4. The sectors we work inWhile the brochure needs to have a certain corporate feel to it, we don't want it to be "boring" or "stiff". We would like it to have a slightly "friendly" or "informal" feel to it, to reflect the type of organisation we are.We have a company website http://brevalconsultingpartners.net , however we do not want to directly replicate the content or feel as we recognise it needs updating.We would like the brochure to be A4 portrait format. We anticipate requiring 12 sides (including covers) but we are happy to be guided on this based on the content we have provided.The attached ppt file gives the detail of the content to be included and also shows the proposed pagination. For the front cover we would like to try 2 versions, one with the BCP logo and one with the Breval Consulting Partners logo (a file of both is attached)One of the most important pages will be the "Our Services" page. We would like this to cover the centre fold. In the ppt file we have shown an example layout, but this is where we need most help - we are clearly not graphic designers! This page will be the most used page in sales meetings etc.Also attached is the following:1. file for our BrevalConsulting Partners company logo.2. File for our BCP company logo3. Files for Derek's signatures (for under photos) - Owen's to follow4. Photo of Derek & Owen (person in purple shirt to be cropped out)Thank you and really excited to see what everyone comes back with.Derek & Owen

Target Market(s)

Very broad - Manufacturing, Healthcare, Hospitality

Industry/Entity Type

Management Consulting

Font styles to use
Other font styles liked:
• We use Swiss721, but happy to be guided by designer

Colors
3276b5
85abd2
0355a3
333333
5c5c5c
9d9d9d
d9d9d9

Requirements
Must have
• Corporate feel
Nice to have
• Slightly friendly feel
• Our standard "blue" is (CORRECTION) - R55 G96 B146 #376092 and our standard grey is R197 G178, B179 - #B3B2B2, which we would like to keep, but other colours we are happy to be guided on. Brand guidelines attached.

```html
<!DOCTYPE html>
<html lang="en">
<head>
<meta charset="utf-8">
<title>Our Approach</title>
<link href="https://fonts.googleapis.com/css2?family=Open+Sans:wght@400;600;700;800&display=swap" rel="stylesheet">
<style>
  :root {
    --brand-blue: #1f4fd6;
    --deep-blue: #0033a0;
    --sky-blue: #4ea0f5;
    --cyan: #2ec0f2;
    --steel: #3b5a70;
    --charcoal: #333333;
    --panel-grey: #dfe4e6;
    --slate-grey: #c8d2d6;
    --text: #111111;
  }
  * { margin: 0; padding: 0; box-sizing: border-box; }
  html, body { width: 848px; height: 1200px; overflow: hidden; background: #fff; }
  body { font-family: "Open Sans", sans-serif; color: var(--text); }
  .page { position: relative; width: 848px; height: 1200px; overflow: hidden; }

  .header-band {
    position: absolute; left: 0; top: 0; width: 848px; height: 122px;
    background: linear-gradient(90deg, #1840d0 0%, #2d5fe6 55%, #4a8cf0 80%, #6fb0f7 100%);
  }
  .header-skyline {
    position: absolute; right: 0; top: 0; width: 330px; height: 122px;
    background: linear-gradient(90deg, rgba(90,150,240,0) 0%, rgba(120,180,250,.55) 40%, rgba(30,70,170,.5) 100%);
  }
  .header-rule { position: absolute; left: 0; top: 122px; width: 848px; height: 7px; background: var(--charcoal); }
  .page-title {
    position: absolute; left: 562px; top: 66px;
    font-family: "Open Sans", sans-serif; font-weight: 700; font-size: 33px; color: #fff;
    letter-spacing: -0.3px;
  }

  .diagram { position: absolute; left: 0; top: 0; }

  .intro {
    position: absolute; left: 95px; top: 750px; width: 672px;
    font-weight: 700; font-size: 16px; line-height: 25.6px; text-align: justify; letter-spacing: .3px;
  }
  .body-copy {
    position: absolute; left: 95px; top: 828px; width: 672px;
    font-size: 16px; line-height: 25.6px; text-align: justify; letter-spacing: .2px;
  }

  .page-number { position: absolute; left: 787px; top: 1131px; font-size: 20px; color: var(--text); }
</style>
</head>
<body>
<div class="page">
  <div class="header-band"></div>
  <div class="header-skyline" role="img" aria-label="City skyline photograph"></div>
  <div class="header-rule"></div>
  <h1 class="page-title">Our Approach</h1>

  <svg class="diagram" width="848" height="1200" viewBox="0 0 848 1200" font-family="Open Sans, sans-serif">
    <defs>
      <linearGradient id="deliveryFill" x1="0" y1="0" x2="0" y2="1">
        <stop offset="0" stop-color="#2f7df0"/><stop offset="1" stop-color="#5cd2fb"/>
      </linearGradient>
      <linearGradient id="stageFill" x1="0" y1="0" x2="0" y2="1">
        <stop offset="0" stop-color="#4a4a4a"/><stop offset="1" stop-color="#1a1a1a"/>
      </linearGradient>
      <linearGradient id="coachFill" x1="0" y1="0" x2="1" y2="0">
        <stop offset="0" stop-color="#3b5a70"/><stop offset="1" stop-color="#2ec0f2"/>
      </linearGradient>
      <linearGradient id="kpiFill" x1="0" y1="0" x2="1" y2="0">
        <stop offset="0" stop-color="#2a64ec"/><stop offset="1" stop-color="#00279a"/>
      </linearGradient>
    </defs>

    <!-- process panel -->
    <rect x="93" y="250" width="675" height="160" fill="#dfe4e6"/>

    <!-- initial engagement -->
    <rect x="100" y="268" width="107" height="131" fill="#2a5fc8"/>
    <rect x="103" y="268" width="104" height="127" fill="#3a7ae0"/>
    <polygon points="204,303 222,303 222,290 240,318 222,346 222,333 204,333" fill="#3a7ae0" stroke="#2a5fc8"/>
    <g fill="#fff" font-size="13" text-anchor="middle">
      <text x="154" y="311">INITIAL</text>
      <text x="154" y="327">ENGAGEMENT</text>
      <text x="154" y="344">&amp; STRATEGIC</text>
      <text x="154" y="360">PLANNING</text>
    </g>

    <!-- project delivery -->
    <rect x="240" y="264" width="387" height="98" fill="#c9d1d4"/>
    <rect x="243" y="267" width="381" height="92" fill="url(#deliveryFill)"/>
    <text x="427" y="319" fill="#fff" font-size="17" font-weight="800" text-anchor="middle" letter-spacing="1">PROJECT DELIVERY</text>

    <!-- monitor & support -->
    <rect x="656" y="268" width="107" height="131" fill="#1e48b8"/>
    <rect x="656" y="268" width="103" height="127" fill="#2e62d8"/>
    <polygon points="664,303 646,303 646,290 626,318 646,346 646,333 664,333" fill="#2e62d8" stroke="#1e48b8"/>
    <g fill="#fff" font-size="13" text-anchor="middle">
      <text x="709" y="322">MONITOR &amp;</text>
      <text x="709" y="338">CONTINUED</text>
      <text x="709" y="355">SUPPORT</text>
    </g>

    <!-- stage arrows -->
    <g stroke="#9fb0b6" stroke-dasharray="3 3" stroke-width="1.5">
      <line x1="280" y1="361" x2="280" y2="378"/><line x1="379" y1="361" x2="379" y2="378"/>
      <line x1="483" y1="361" x2="483" y2="378"/><line x1="584" y1="361" x2="584" y2="378"/>
    </g>
    <g fill="#9fb0b6">
      <polygon points="273,377 287,377 280,389"/><polygon points="372,377 386,377 379,389"/>
      <polygon points="476,377 490,377 483,389"/><polygon points="577,377 591,377 584,389"/>
    </g>

    <!-- stages -->
    <g stroke="#4f5e64" stroke-width="2">
      <rect x="226" y="393" width="98" height="60" fill="url(#stageFill)"/>
      <rect x="330" y="393" width="97" height="60" fill="url(#stageFill)"/>
      <rect x="433" y="393" width="97" height="60" fill="url(#stageFill)"/>
      <rect x="537" y="393" width="97" height="60" fill="url(#stageFill)"/>
    </g>
    <g fill="#fff" font-size="7.5" font-weight="700" text-anchor="middle">
      <text x="275" y="421">LAUNCH &amp;</text><text x="275" y="430">DIAGNOSTIC</text>
      <text x="378" y="427">IMPLEMENTATION</text>
      <text x="484" y="414">MONITOR &amp;</text><text x="484" y="423">REPORT</text><text x="484" y="432">PROGRESS</text>
      <text x="586" y="421">CONFIRMATION</text><text x="586" y="430">&amp; CLOSE</text>
    </g>

    <!-- outcome arrows -->
    <polygon points="162,475 424,475 424,547 204,547 204,602 225,602 184,650 143,602 162,602" fill="url(#coachFill)"/>
    <polygon points="435,475 697,475 697,602 718,602 677,650 636,602 656,602 656,547 435,547" fill="url(#kpiFill)"/>
    <g fill="#fff" font-size="10" font-weight="700" text-anchor="middle" letter-spacing=".4">
      <text x="299" y="509">COACHING AND KNOWLEDGE</text><text x="299" y="521">TRANSFER</text>
      <text x="560" y="509">PERFORMANCE MEASUREMENT</text><text x="560" y="521">(KERY PERFORMANCE INDICATORS)</text>
    </g>

    <!-- footer -->
    <polygon points="848,936 682,1200 848,1200" fill="#c8d2d6"/>
    <polygon points="0,1120 764,1120 714,1200 0,1200" fill="#1f45c2"/>
    <line x1="0" y1="1121" x2="763" y2="1121" stroke="#0f2f9a" stroke-width="2"/>
    <polygon points="784,1164 848,1164 848,1180 774,1180" fill="#3f4d52"/>
  </svg>

  <p class="intro">Before everything else, our approach is collaborative.&nbsp; This key principle means we develop programmes of work and an approach to suit your needs.</p>

  <p class="body-copy">Throughout our engagements we employ an effective, yet simple set of tools and techniques to ensure we keep on track to guarantee delivery and achieve results. However, our view is that if we just deliver a great set of results we have only partly succeeded, real success has to include the development of your team and leaving them with a set of skills and know-how gained from working alongside us.&nbsp; Our sleeves rolled up style gets things done through showing, not just telling.</p>

  <div class="page-number">9</div>
</div>
</body>
</html>
```